Private Investigation Business Card Design

I need a business card for a new private investigation company named Brisk Inquiries. I perform mainly surveillance jobs, vehicle repossessions, document serves etc. The final design should aim for a professional look. The logo has a magnifying glass with stick man arms and legs and is in a running action to show the "Brisk" aspect of the name. If the colour scheme could remain the same as the website www.briskinquiries-demo.com.au with silvers,blacks and a couple electric blue highlights.
Industry/Entity Type
Business
Contact Information for Business Card
Morgan Kellaway
Brisk Inquiries
0487316204
PO Box 58, Carnwell NSW 2291
info@briskinquiries-demo.com.au
www.briskinquiries-demo.com.au
Look and feel

```html
<!DOCTYPE html>
<html lang="en">
<head>
<meta charset="utf-8">
<title>Brisk Inquiries – Business Card</title>
<link href="https://fonts.googleapis.com/css2?family=Arimo:wght@400;700&display=swap" rel="stylesheet">
<style>
  :root {
    --stage: #2b2b2d;
    --card-white: #ffffff;
    --card-dark: #282526;
    --electric-blue: #2a9fe4;
    --ink: #1c1c1c;
    --silver: #8b8e92;
    --silver-mid: #b4b7bb;
    --silver-light: #d3d5d8;
    --text-light: #f2f2f2;
  }
  * { box-sizing: border-box; margin: 0; padding: 0; }
  html, body {
    width: 1200px; height: 750px; overflow: hidden;
    background: var(--stage);
    font-family: "Arimo", Arial, sans-serif;
  }
  .stage {
    width: 1200px; height: 750px;
    display: flex; align-items: center; justify-content: center; gap: 56px;
  }
  .card {
    width: 520px; height: 316px;
    position: relative; overflow: hidden;
    box-shadow: 0 14px 30px rgba(0,0,0,0.45);
  }

  /* Front */
  .card--front { background: var(--card-white); }
  .mascot-art {
    position: absolute; left: 150px; top: 40px;
    width: 230px; height: 150px;
    border-radius: 10px;
    background: linear-gradient(160deg, var(--silver-light) 0%, var(--silver-mid) 50%, #e6e7e9 100%);
  }
  .social-row {
    position: absolute; left: 90px; top: 206px; width: 340px; height: 30px;
  }
  .social-row .rule {
    position: absolute; left: 0; right: 0; top: 50%;
    height: 1px;
    background: linear-gradient(90deg, transparent, var(--silver) 30%, var(--silver) 70%, transparent);
  }
  .social-row .dots {
    position: absolute; left: 50%; top: 50%; transform: translate(-50%, -50%);
    display: flex; gap: 5px; background: var(--card-white); padding: 0 8px;
  }
  .social-row .dot {
    width: 18px; height: 18px; border-radius: 50%;
    background: var(--ink);
    box-shadow: inset 0 0 0 2px var(--card-white), 0 0 0 1px var(--ink);
  }

  /* Back */
  .card--back { display: flex; }
  .contact-panel {
    width: 50%; background: var(--card-dark);
    padding: 74px 0 0 34px; color: var(--text-light);
  }
  .contact-name {
    color: var(--electric-blue); font-size: 21px; font-weight: 700;
    margin-bottom: 18px; letter-spacing: 0.2px;
  }
  .contact-address { font-size: 12px; line-height: 16px; margin-bottom: 8px; }
  .contact-list { list-style: none; font-size: 12px; line-height: 19px; }
  .contact-list li { display: flex; align-items: center; gap: 8px; }
  .contact-list svg { width: 12px; height: 12px; flex: none; fill: var(--electric-blue); }
  .brand-panel {
    width: 50%; background: var(--card-white);
    display: flex; align-items: center; justify-content: center; gap: 10px;
  }
  .brand-name {
    font-size: 25px; font-weight: 700; color: var(--silver);
    letter-spacing: 0.5px;
  }
  .brand-mark {
    width: 14px; height: 14px; border-radius: 50%; background: var(--silver-light);
  }
</style>
</head>
<body>
<main class="stage">
  <section class="card card--front" aria-label="Card front">
    <div class="mascot-art" role="img" aria-label="Running magnifying-glass mascot with stick arms and legs and speed lines"></div>
    <div class="social-row" aria-label="Social links">
      <span class="rule"></span>
      <div class="dots">
        <span class="dot"></span><span class="dot"></span><span class="dot"></span><span class="dot"></span>
      </div>
    </div>
  </section>

  <section class="card card--back" aria-label="Card back">
    <div class="contact-panel">
      <h1 class="contact-name">Morgan Kellaway</h1>
      <p class="contact-address">PO Box 58<br>Carnwell NSW 2291</p>
      <ul class="contact-list">
        <li>
          <svg viewBox="0 0 24 24" aria-hidden="true"><path d="M6.6 10.8a15.1 15.1 0 0 0 6.6 6.6l2.2-2.2c.3-.3.7-.4 1-.2 1.1.4 2.3.6 3.6.6.6 0 1 .4 1 1V20c0 .6-.4 1-1 1A17 17 0 0 1 3 4c0-.6.4-1 1-1h3.5c.6 0 1 .4 1 1 0 1.3.2 2.5.6 3.6.1.3 0 .7-.2 1z"/></svg>
          0487 316 204
        </li>
        <li>
          <svg viewBox="0 0 24 24" aria-hidden="true"><path d="M2 5h20v14H2zm2 2v.5l8 5 8-5V7l-8 5z"/></svg>
          info@briskinquiries-demo.com.au
        </li>
        <li>
          <svg viewBox="0 0 24 24" aria-hidden="true"><circle cx="12" cy="12" r="10"/></svg>
          www.briskinquiries-demo.com.au
        </li>
      </ul>
    </div>
    <div class="brand-panel">
      <span class="brand-name">Brisk Inquiries</span>
      <span class="brand-mark" aria-hidden="true"></span>
    </div>
  </section>
</main>
</body>
</html>
```